Vantor Wear and Fuel is looking for a Clothing/Supplement Online Store Website!

Must be convenient, and user friendly, with vibrant colors that catch the eye!

Target Market(s)

Athletes, and Fashion Customers

Industry/Entity Type

Fitness

Coding

Coded - Design and coding required

Number of Pages Required

3 page

Font styles to use
Decorative

Colors

Designer to choose colors to be used in the design.

Requirements
Must have
• Somewhere to feature products, features to promote discounts and make announcements.
Nice to have
• My logos on each page

```html
<!DOCTYPE html>
<html lang="en">
<head>
<meta charset="utf-8">
<title>Vantor Wear and Fuel</title>
<link href="https://fonts.googleapis.com/css2?family=Poppins:wght@400;500;600;700&family=Roboto:wght@400;500;700&display=swap" rel="stylesheet">
<style>
:root{
  --gold:#b8823a;
  --gold-dark:#a06f2c;
  --teal:#3ba9a5;
  --ink:#2b2b2b;
  --text:#444;
  --muted:#777;
  --light:#f1f1f1;
  --footer:#242424;
  --footer-bottom:#1d1d1d;
  --white:#fff;
}
*{box-sizing:border-box;margin:0;padding:0}
html,body{width:1200px;height:4594px;overflow:hidden}
body{font-family:"Poppins",sans-serif;color:var(--text);background:var(--white);position:relative}
.abs{position:absolute}
section,header,footer{position:absolute;left:0;width:1200px}

/* top bar */
.topbar{top:0;height:30px;background:var(--gold);color:var(--white);font-family:"Roboto",sans-serif;font-size:13px}
.topbar .left{left:143px;top:7px;display:flex;gap:6px;align-items:center}
.topbar .right{right:143px;top:7px;display:flex;gap:30px;align-items:center;font-weight:500}
.topbar .right span{display:flex;gap:7px;align-items:center}

/* header */
.site-header{top:30px;height:104px;background:var(--white)}
.brand{left:143px;top:32px;font-family:"Poppins",sans-serif;font-weight:600;font-size:36px;letter-spacing:1px;color:#333;display:flex;align-items:center;gap:10px}
.brand .dot{width:14px;height:14px;background:var(--gold)}
.nav{left:413px;top:44px;display:flex;gap:28px;font-family:"Roboto",sans-serif;font-size:15px;color:#333}
.nav .active{color:var(--gold)}
.nav-icons{left:990px;top:40px;display:flex;gap:18px}

/* hero */
.hero{top:134px;height:624px;background:linear-gradient(180deg,#40b2ad,#33a19d)}
.hero-photo{left:560px;top:0;width:640px;height:624px;background:radial-gradient(ellipse at 55% 55%,#c9b28d 0%,#a98fa8 35%,rgba(59,169,165,0) 70%)}
.hero h1{left:143px;top:182px;font-size:47px;font-weight:700;color:var(--white);letter-spacing:.5px}
.hero p{left:143px;top:250px;width:470px;font-size:19px;line-height:34px;color:var(--white)}
.btn-light{left:143px;top:340px;width:134px;height:38px;background:var(--white);border-radius:3px;font-size:13px;font-weight:600;color:#333;display:flex;align-items:center;justify-content:center;box-shadow:0 2px 4px rgba(0,0,0,.2)}
.hero-arrow{width:40px;height:40px;border:2px solid rgba(255,255,255,.8);border-radius:50%;display:flex;align-items:center;justify-content:center}

/* features */
.features{top:758px;height:108px;background:var(--light)}
.feature{top:32px;display:flex;gap:18px;align-items:flex-start}
.feature h4{font-size:17px;font-weight:600;color:#333;line-height:22px}
.feature p{font-size:12px;color:#555;margin-top:4px}

/* product sections */
.framed{border:5px solid var(--gold)}
.photo{display:block}
.eyebrow{font-size:16px;font-weight:500;color:#333;letter-spacing:.3px}
.section-title{font-size:27px;font-weight:600;color:#333;letter-spacing:.8px}
.small-arrow{width:22px;height:22px;border:1.5px solid #555;border-radius:50%;display:flex;align-items:center;justify-content:center}
.sale{position:absolute;top:10px;right:8px;background:var(--gold);color:var(--white);font-size:9px;font-weight:700;padding:2px 7px}
.prod-text{font-size:14px;line-height:21px;color:#333}
.price{font-size:14px;color:var(--gold);margin-top:6px}
.price s{color:#999;margin-right:4px}

/* sale banner */
.sale-banner{top:2109px;height:541px;background:linear-gradient(90deg,#ece7ea 0%,#e5dfe3 45%,#d6cfd3 100%)}
.sale-word{font-family:"Poppins",sans-serif;font-weight:700;font-size:128px;color:#bcb4b8;line-height:1;letter-spacing:4px}
.flat-badge{left:177px;top:160px;width:226px;height:226px;border-radius:50%;background:var(--gold);border:4px solid rgba(255,255,255,.7);color:var(--white);text-align:center}

/* featured */
.featured{top:2650px;height:688px;background:var(--light)}
.center-title{left:0;width:1200px;text-align:center;font-size:36px;font-weight:600;color:#333}
.rule{left:567px;width:66px;height:3px;background:var(--gold)}
.card{top:176px;width:209px;height:423px;background:var(--white);box-shadow:0 2px 6px rgba(0,0,0,.15);text-align:center}
.card .photo{margin:9px auto 0;width:191px;height:251px}
.card h5{font-family:"Roboto",sans-serif;font-size:14px;font-weight:500;color:#333;line-height:22px;margin-top:18px}
.card .promo{font-family:"Roboto",sans-serif;font-style:italic;font-size:13px;color:var(--gold);margin-top:8px}
.btn-gold{display:inline-flex;margin-top:12px;height:30px;padding:0 20px;align-items:center;background:var(--gold);color:var(--white);font-size:13px;font-weight:600;border-radius:15px}
.big-arrow{width:34px;height:34px;border:1.5px solid #444;border-radius:50%;display:flex;align-items:center;justify-content:center}

/* news */
.news{top:3338px;height:531px;background:var(--white)}
.news-item{top:171px;width:280px}
.news-item .photo{width:280px;height:177px;border:4px solid #e3e3e3}
.news-date{font-family:"Roboto",sans-serif;font-size:13px;color:var(--gold);margin-top:32px;display:flex;gap:6px;align-items:center}
.news-date em{font-style:normal;color:#555;font-size:12px;margin-left:6px}
.news-item p{font-family:"Roboto",sans-serif;font-size:15px;color:#333;line-height:25px;margin-top:8px}

/* newsletter */
.newsletter{top:3869px;height:253px;background:var(--gold);color:var(--white);text-align:center}
.newsletter h2{position:absolute;left:0;width:1200px;top:40px;font-size:38px;font-weight:600;letter-spacing:.5px}
.newsletter p{position:absolute;left:0;width:1200px;top:98px;font-family:"Roboto",sans-serif;font-size:15px;line-height:24px}
.nl-input{left:326px;top:165px;width:426px;height:40px;background:var(--white);border-radius:20px;color:#777;font-size:11px;text-align:left;padding:12px 18px}
.nl-btn{left:759px;top:165px;width:115px;height:40px;background:#222;border-radius:20px;font-size:13px;font-weight:600;display:flex;align-items:center;justify-content:center}

/* footer */
.footer{top:4122px;height:389px;background:var(--footer);color:#ddd}
.footer h6{font-size:17px;font-weight:600;color:var(--white);letter-spacing:.3px}
.contact-list{font-size:13px;line-height:19px}
.contact-row{display:flex;gap:18px;margin-bottom:12px}
.link-list{list-style:none;font-size:12px;line-height:29px}
.link-list li::before{content:"›";margin-right:10px}
.foot-brand{font-size:36px;font-weight:600;color:var(--white);letter-spacing:1px}
.pay{display:flex;gap:4px}
.pay span{width:46px;height:26px;border-radius:2px}
.social{display:flex;gap:9px}
.social span{width:32px;height:32px;border:1.5px solid #ccc;border-radius:50%}
.bottom-bar{top:4511px;height:83px;background:var(--footer-bottom);color:#ddd;font-size:13px;text-align:center;line-height:83px}
</style>
</head>
<body>

<div class="abs topbar" style="left:0;width:1200px">
  <div class="abs left">
    <svg width="13" height="11" viewBox="0 0 13 11"><path d="M1 6l4 4 7-9" fill="none" stroke="#fff" stroke-width="2"/></svg>
    30 Day Return Right
  </div>
  <div class="abs right">
    <span><svg width="12" height="12" viewBox="0 0 12 12"><path d="M2 1l3 1 -1 3c1 2 2 3 4 4l3-1 1 3-2 1C5 11 1 7 1 3z" fill="#fff"/></svg>800 4120 7730</span>
    <span><svg width="11" height="13" viewBox="0 0 11 13"><rect x="1" y="6" width="9" height="7" fill="#fff"/><path d="M3 6V4a2.5 2.5 0 015 0v2" fill="none" stroke="#fff" stroke-width="1.6"/></svg>REGISTER</span>
    <span><svg width="13" height="13" viewBox="0 0 13 13"><circle cx="6.5" cy="6.5" r="6" fill="#fff"/><circle cx="6.5" cy="5" r="2" fill="#b8823a"/><path d="M3 10.5c1-2 6-2 7 0" fill="#b8823a"/></svg>LOGIN</span>
  </div>
</div>

<header class="site-header">
  <div class="abs brand"><span class="dot"></span>Vantor</div>
  <nav class="abs nav">
    <span class="active">HOME</span><span>ABOUT</span><span>APPAREL AND NUTRITION</span><span>SHOP</span><span>BLOG</span><span>CONTACT</span>
  </nav>
  <div class="abs nav-icons">
    <svg width="28" height="26" viewBox="0 0 28 26"><path d="M1 3h5l4 14h14l3-10H8" fill="none" stroke="#333" stroke-width="2"/><circle cx="12" cy="22" r="2" fill="#333"/><circle cx="22" cy="22" r="2" fill="#333"/><circle cx="22" cy="5" r="4" fill="#b8823a"/></svg>
    <svg width="20" height="22" viewBox="0 0 20 22"><circle cx="8" cy="10" r="6" fill="none" stroke="#333" stroke-width="2.5"/><path d="M12.5 14.5l5 5" stroke="#333" stroke-width="2.5"/></svg>
  </div>
</header>

<section class="hero">
  <div class="abs hero-photo" role="img" aria-label="Fashion model in a green knit top and pastel skirt seated against a teal backdrop"></div>
  <h1 class="abs">VANTOR WEAR</h1>
  <p class="abs">Nemo enim ipsam voluptatem quia voluptas sit aspernatur aut odit</p>
  <div class="abs btn-light">SHOP NOW</div>
  <div class="abs hero-arrow" style="left:47px;top:268px"><svg width="12" height="14" viewBox="0 0 12 14"><path d="M9 1L3 7l6 6" fill="none" stroke="#fff" stroke-width="2"/></svg></div>
  <div class="abs hero-arrow" style="left:1112px;top:262px"><svg width="12" height="14" viewBox="0 0 12 14"><path d="M3 1l6 6-6 6" fill="none" stroke="#fff" stroke-width="2"/></svg></div>
</section>

<section class="features">
  <div class="abs feature" style="left:60px">
    <svg width="44" height="34" viewBox="0 0 44 34"><path d="M2 6h24v20H2zM26 12h9l6 7v7H26" fill="none" stroke="#3b5b8c" stroke-width="2"/><circle cx="10" cy="28" r="3.5" fill="#fff" stroke="#3b5b8c" stroke-width="2"/><circle cx="33" cy="28" r="3.5" fill="#fff" stroke="#3b5b8c" stroke-width="2"/></svg>
    <div><h4>FREE RETURNS</h4><p>Duis aute irure dolor in</p></div>
  </div>
  <div class="abs feature" style="left:315px">
    <svg width="40" height="34" viewBox="0 0 40 34"><path d="M5 22V17a15 15 0 0130 0v5" fill="none" stroke="#3b5b8c" stroke-width="2"/><rect x="3" y="19" width="7" height="12" rx="2" fill="none" stroke="#3b5b8c" stroke-width="2"/><rect x="30" y="19" width="7" height="12" rx="2" fill="none" stroke="#3b5b8c" stroke-width="2"/></svg>
    <div><h4>ONLINE SUPPORT</h4><p>Lorem ipsum dolor sit amet</p></div>
  </div>
  <div class="abs feature" style="left:602px">
    <svg width="40" height="40" viewBox="0 0 40 40"><circle cx="20" cy="20" r="17" fill="none" stroke="#3b5b8c" stroke-width="2"/><circle cx="20" cy="20" r="11" fill="none" stroke="#3b5b8c" stroke-width="2"/><path d="M20 13v8h5" fill="none" stroke="#3b5b8c" stroke-width="2"/></svg>
    <div><h4>48 HRS SHIPPING</h4><p>V / booking before kl. 16.30 Mon-Fri</p></div>
  </div>
  <div class="abs feature" style="left:922px">
    <svg width="56" height="34" viewBox="0 0 56 34"><rect x="2" y="4" width="52" height="26" fill="none" stroke="#3b5b8c" stroke-width="2"/><rect x="7" y="8" width="42" height="18" fill="none" stroke="#3b5b8c" stroke-width="1.5"/><circle cx="28" cy="17" r="6" fill="none" stroke="#3b5b8c" stroke-width="2"/></svg>
    <div><h4>EASY PAYMENT</h4><p>For purchases from 499</p></div>
  </div>
</section>

<!-- casual dresses -->
<div class="abs framed" style="left:130px;top:950px;width:380px;height:460px;border-right:none;border-bottom-color:var(--gold)"></div>
<div class="abs photo" role="img" aria-label="Couple in sunglasses, man in grey blazer and woman in floral dress, against a blue wall" style="left:148px;top:968px;width:369px;height:446px;background:linear-gradient(120deg,#3f7fc4 0%,#8fa6c0 45%,#e8d8cf 100%)"></div>
<div class="abs eyebrow" style="left:565px;top:962px">VANTOR WEAR</div>
<div class="abs section-title" style="left:565px;top:984px">CASUAL DRESSES</div>
<div class="abs small-arrow" style="left:1014px;top:972px"><svg width="8" height="10" viewBox="0 0 8 10"><path d="M6 1L2 5l4 4" fill="none" stroke="#555" stroke-width="1.5"/></svg></div>
<div class="abs small-arrow" style="left:1044px;top:972px"><svg width="8" height="10" viewBox="0 0 8 10"><path d="M2 1l4 4-4 4" fill="none" stroke="#555" stroke-width="1.5"/></svg></div>

<div class="abs" style="left:567px;top:1054px;width:228px">
  <div class="photo" role="img" aria-label="Man in denim shirt and beige chinos on white" style="position:relative;width:228px;height:273px;background:linear-gradient(180deg,#e9ecee,#cfd6dc)"><span class="sale">SALE!</span></div>
  <p class="prod-text" style="margin-top:14px">Sed ut perspiciatis unde omnis iste natus sit voluptatem</p>
  <p class="price"><s>$95.00</s>$75.00</p>
</div>
<div class="abs" style="left:838px;top:1054px;width:228px">
  <div class="photo" role="img" aria-label="Woman in blue dress with red handbag on pink" style="position:relative;width:228px;height:273px;background:linear-gradient(180deg,#f4b7cc,#ea8fb0)"><span class="sale">SALE!</span></div>
  <p class="prod-text" style="margin-top:14px">Sed ut perspiciatis unde omnis iste natus sit voluptatem</p>
  <p class="price"><s>$95.00</s>$75.00</p>
</div>

<!-- supplement store -->
<div class="abs eyebrow" style="left:130px;top:1532px">VANTOR FUEL</div>
<div class="abs section-title" style="left:130px;top:1554px">SUPPLEMENT STORE</div>
<div class="abs small-arrow" style="left:577px;top:1542px"><svg width="8" height="10" viewBox="0 0 8 10"><path d="M6 1L2 5l4 4" fill="none" stroke="#555" stroke-width="1.5"/></svg></div>
<div class="abs small-arrow" style="left:607px;top:1542px"><svg width="8" height="10" viewBox="0 0 8 10"><path d="M2 1l4 4-4 4" fill="none" stroke="#555" stroke-width="1.5"/></svg></div>
<div class="abs" style="left:130px;top:1624px;width:228px">
  <div class="photo" role="img" aria-label="White pill bottle with spilled tablets on teal" style="position:relative;width:228px;height:273px;background:linear-gradient(160deg,#5fa3b4,#d9e6ea 60%,#8bb8c4)"><span class="sale">SALE!</span></div>
  <p class="prod-text" style="margin-top:14px">Sed ut perspiciatis unde omnis iste natus sit voluptatem</p>
  <p class="price"><s>$95.00</s>$75.00</p>
</div>
<div class="abs" style="left:403px;top:1624px;width:228px">
  <div class="photo" role="img" aria-label="Two black supplement tubs with orange lids" style="position:relative;width:228px;height:273px;background:linear-gradient(180deg,#3a3a3a,#111 70%,#e6e6e6)"><span class="sale">SALE!</span></div>
  <p class="prod-text" style="margin-top:14px">Sed ut perspiciatis unde omnis iste natus sit voluptatem</p>
  <p class="price"><s>$95.00</s>$75.00</p>
</div>
<div class="abs framed" style="left:683px;top:1528px;width:368px;height:446px;border-left-width:5px;border-right:none;border-top-width:5px"></div>
<div class="abs photo" role="img" aria-label="Smiling woman holding a supplement capsule and bottle" style="left:699px;top:1544px;width:367px;height:447px;background:linear-gradient(135deg,#d8dadb 0%,#c8a88f 45%,#9cd3cf 100%)"></div>

<!-- sale banner -->
<section class="sale-banner">
  <div class="abs photo" role="img" aria-label="Man in sunglasses, hat and denim shirt reclining on the floor" style="left:520px;top:0;width:680px;height:541px;background:radial-gradient(ellipse at 55% 50%,#b89b7c 0%,#c8b6a8 35%,rgba(220,213,218,0) 72%)"></div>
  <div class="abs sale-word" style="left:140px;top:30px">SALE</div>
  <div class="abs sale-word" style="left:85px;top:165px">OFFER</div>
  <div class="abs flat-badge">
    <div style="position:absolute;left:42px;top:44px;font-size:48px;font-weight:600;line-height:1">FLAT</div>
    <div style="position:absolute;left:40px;top:96px;font-size:72px;font-weight:600;line-height:1">35<span style="font-size:50px">%</span></div>
    <div style="position:absolute;left:140px;top:96px;font-size:20px;font-weight:500">Off</div>
  </div>
</section>

<!-- featured -->
<section class="featured">
  <h2 class="abs center-title" style="top:58px">FEATURED PRODUCTS</h2>
  <div class="abs rule" style="top:124px"></div>
  <div class="abs big-arrow" style="left:57px;top:353px"><svg width="10" height="12" viewBox="0 0 10 12"><path d="M7 1L2 6l5 5" fill="none" stroke="#444" stroke-width="1.5"/></svg></div>
  <div class="abs big-arrow" style="left:1073px;top:353px"><svg width="10" height="12" viewBox="0 0 10 12"><path d="M3 1l5 5-5 5" fill="none" stroke="#444" stroke-width="1.5"/></svg></div>

  <div class="abs card" style="left:128px">
    <div class="photo" role="img" aria-label="Open bottle with capsules on wooden table" style="background:linear-gradient(180deg,#e8e4df,#a67c52)"></div>
    <h5>NEMO ENIM IPSAM<br>VOLUPTATEM QUIA VOLU</h5>
    <p class="promo">Promo Code: 25JGD4</p>
    <span class="btn-gold">ADD TO CART</span>
  </div>
  <div class="abs card" style="left:362px">
    <div class="photo" role="img" aria-label="Red-haired woman in denim jacket" style="background:linear-gradient(180deg,#ececec,#b7c6d8)"></div>
    <h5>NEMO ENIM IPSAM<br>VOLUPTATEM QUIA VOLU</h5>
    <p class="promo">Promo Code: 25JGD4</p>
    <span class="btn-gold">ADD TO CART</span>
  </div>
  <div class="abs card" style="left:596px">
    <div class="photo" role="img" aria-label="Supplement tubs with spilled capsules" style="background:linear-gradient(180deg,#f2f2f2,#5b8a3a 55%,#d7b46a)"></div>
    <h5>NEMO ENIM IPSAM<br>VOLUPTATEM QUIA VOLU</h5>
    <p class="promo">Promo Code: 25JGD4</p>
    <span class="btn-gold">ADD TO CART</span>
  </div>
  <div class="abs card" style="left:829px">
    <div class="photo" role="img" aria-label="Man in tan jacket and black tank top" style="background:linear-gradient(180deg,#2f2f2f,#a8744a 60%,#3a3a3a)"></div>
    <h5>NEMO ENIM IPSAM<br>VOLUPTATEM QUIA VOLU</h5>
    <p class="promo">Promo Code: 25JGD4</p>
    <span class="btn-gold">ADD TO CART</span>
  </div>
</section>

<!-- news -->
<section class="news">
  <h2 class="abs center-title" style="top:64px">LATEST NEWS</h2>
  <div class="abs rule" style="top:130px"></div>
  <div class="abs news-item" style="left:143px">
    <div class="photo" role="img" aria-label="Capsules among fresh vegetables" style="background:linear-gradient(135deg,#4f5b3a,#8a6f9a 50%,#c8b07a)"></div>
    <div class="news-date">▦ Oct 01, 2019,<em>36 mins ago</em></div>
    <p>Nemo enim ipsam voluptatem quia voluptas sit aspernatur</p>
  </div>
  <div class="abs news-item" style="left:459px">
    <div class="photo" role="img" aria-label="Woman in a city street at sunset" style="background:linear-gradient(180deg,#9aa4ad,#d8b58a 60%,#6b5a4a)"></div>
    <div class="news-date">▦ Oct 01, 2019,<em>36 mins ago</em></div>
    <p>Nemo enim ipsam voluptatem quia voluptas sit aspernatur</p>
  </div>
  <div class="abs news-item" style="left:775px">
    <div class="photo" role="img" aria-label="Athlete filming a video in a kitchen" style="background:linear-gradient(180deg,#e6e6e6,#9a9a9a 55%,#d9c7b8)"></div>
    <div class="news-date">▦ Oct 01, 2019,<em>36 mins ago</em></div>
    <p>Nemo enim ipsam voluptatem quia voluptas sit aspernatur</p>
  </div>
</section>

<!-- newsletter -->
<section class="newsletter">
  <h2>JOIN OUR NEWSLETTER</h2>
  <p>Subscribe to our mailing list to receive updates<br>and promotional offers.</p>
  <div class="abs nl-input">Enter your E - mail</div>
  <div class="abs nl-btn">SUBSCRIBE</div>
</section>

<!-- footer -->
<footer class="footer">
  <h6 class="abs" style="left:143px;top:72px">CONTACT US</h6>
  <div class="abs contact-list" style="left:143px;top:116px;width:260px">
    <div class="contact-row"><svg width="16" height="20" viewBox="0 0 16 20"><path d="M8 1a6 6 0 00-6 6c0 5 6 12 6 12s6-7 6-12a6 6 0 00-6-6z" fill="#fff"/><circle cx="8" cy="7" r="2.3" fill="#242424"/></svg><div>ADDRESS<br>48 Harbour Lane, Kestwick, England</div></div>
    <div class="contact-row"><svg width="16" height="16" viewBox="0 0 12 12"><path d="M2 1l3 1 -1 3c1 2 2 3 4 4l3-1 1 3-2 1C5 11 1 7 1 3z" fill="#fff"/></svg><div>Phone: (214) 309-5561</div></div>
    <div class="contact-row"><svg width="16" height="14" viewBox="0 0 16 14"><rect x="1" y="2" width="14" height="10" fill="#fff"/><path d="M1 2l7 6 7-6" fill="none" stroke="#242424" stroke-width="1.4"/></svg><div>E-mail: hello@vantorwear.com</div></div>
    <div class="contact-row"><svg width="16" height="16" viewBox="0 0 16 16"><circle cx="8" cy="8" r="7" fill="#fff"/><path d="M8 4v4h3" fill="none" stroke="#242424" stroke-width="1.6"/></svg><div>Opening hours:<br><br>Mon-Thurs: 9.30-17.30<br>Fri: 9.30-18.00</div></div>
  </div>
  <h6 class="abs" style="left:440px;top:72px">INFORMATION</h6>
  <ul class="abs link-list" style="left:440px;top:108px">
    <li>Home</li><li>Shop By Brand</li><li>Apparel and Nutrition</li><li>Nutritional Supplements</li><li>Contact</li>
  </ul>
  <h6 class="abs" style="left:633px;top:72px">MY ACCOUNT</h6>
  <ul class="abs link-list" style="left:633px;top:108px">
    <li>Terms &amp; Conditions</li><li>Privacy Policy</li><li>Right of Refusal &amp; Returns</li><li>Cookies</li><li>Shipping &amp; Delivery Terms</li>
  </ul>
  <div class="abs foot-brand" style="left:868px;top:86px">Vantor</div>
  <div class="abs pay" style="left:860px;top:148px">
    <span style="background:#f3f3f3"></span><span style="background:#e8e8e8"></span><span style="background:#dcdcdc"></span><span style="background:#f3f3f3"></span>
  </div>
  <div class="abs social" style="left:940px;top:203px"><span></span><span></span><span></span></div>
</footer>
<div class="abs bottom-bar" style="left:0;width:1200px">© 2019 Vantor. All Rights Reserved.</div>

</body>
</html>
```